New Zealand Marlborough Sauvignon Blanc wine packaging design

We need packaging design for our new wine brand, Dunmore Vale. The wine is a New Zealand Marlborough Sauvignon Blanc. We would like the packaging will portray elegance and style with an understated label. We are looking for a label that portrays the elegance of the French Riviera. The label should be round or pill shaped.
Updates

Industry/Entity Type

Wine

Font styles to use
Serif
Sans Serif

Requirements
Must have
• The words in order of importance: Dunmore Vale, Sauvignon Blanc, Marlborough, New Zealand. It should be fit to the bottle posted in the links
Nice to have
• a pill shape or circular shape
Should not have
• Illustrations of wine bottles, wine glasses, or grapes

```html
<!DOCTYPE html>
<html lang="en">
<head>
<meta charset="utf-8">
<title>Dunmore Vale — Marlborough Sauvignon Blanc Label</title>
<link rel="stylesheet" href="https://fonts.googleapis.com/css2?family=Marcellus&family=Arimo:wght@400&display=swap">
<style>
  :root {
    --ink: #000000;
    --paper: #ffffff;
    --sky-high: #cfcfcf;
    --sky-low: #ededed;
    --horizon: #f6f6f6;
    --shore: #8a8a8a;
    --water: #b4b4b4;
    --water-deep: #6a6a6a;
    --water-edge: #d6d6d6;
    --town-shade: #3a3a3a;
  }
  html, body {
    margin: 0;
    padding: 0;
    width: 705px;
    height: 1200px;
    overflow: hidden;
    background: var(--ink);
  }
  .label {
    display: block;
    width: 705px;
    height: 1200px;
  }
  .label-frame {
    fill: var(--ink);
    stroke: var(--paper);
    stroke-width: 3;
  }
  .scene-edge {
    fill: none;
    stroke: var(--paper);
    stroke-width: 2;
  }
  .brand-name {
    font-family: "Marcellus", serif;
    font-size: 52px;
    letter-spacing: 4px;
    fill: var(--paper);
  }
  .varietal {
    font-family: "Marcellus", serif;
    font-size: 46px;
    letter-spacing: 1px;
    fill: var(--paper);
  }
  .region {
    font-family: "Arimo", sans-serif;
    font-size: 25px;
    letter-spacing: 1px;
    fill: var(--paper);
  }
</style>
</head>
<body>
<svg class="label" viewBox="0 0 705 1200" xmlns="http://www.w3.org/2000/svg">
  <defs>
    <linearGradient id="scene-depth" x1="0" y1="0" x2="0" y2="1">
      <stop offset="0" stop-color="var(--sky-high)"/>
      <stop offset="0.22" stop-color="var(--sky-low)"/>
      <stop offset="0.4" stop-color="var(--horizon)"/>
      <stop offset="0.47" stop-color="var(--shore)"/>
      <stop offset="0.55" stop-color="var(--water)"/>
      <stop offset="0.72" stop-color="var(--water-deep)"/>
      <stop offset="1" stop-color="var(--water-edge)"/>
    </linearGradient>
    <linearGradient id="scene-town" x1="0" y1="0" x2="1" y2="0">
      <stop offset="0" stop-color="var(--town-shade)" stop-opacity="0.7"/>
      <stop offset="0.3" stop-color="var(--town-shade)" stop-opacity="0.35"/>
      <stop offset="0.55" stop-color="var(--town-shade)" stop-opacity="0"/>
    </linearGradient>
    <radialGradient id="scene-glow" cx="0.78" cy="0.45" r="0.35">
      <stop offset="0" stop-color="var(--paper)" stop-opacity="0.75"/>
      <stop offset="1" stop-color="var(--paper)" stop-opacity="0"/>
    </radialGradient>
    <path id="arc-top" d="M 95,600 A 257 320 0 0 1 609,600"/>
    <path id="arc-bottom" d="M 48,600 A 304 368 0 0 0 656,600"/>
  </defs>

  <ellipse class="label-frame" cx="352" cy="600" rx="320" ry="383"/>

  <g class="label-scene" role="img" aria-label="Monochrome drawing of a Riviera harbour town with boats moored along a still, reflective waterfront">
    <ellipse cx="352" cy="600" rx="243" ry="306" fill="url(#scene-depth)"/>
    <ellipse cx="352" cy="600" rx="243" ry="306" fill="url(#scene-town)"/>
    <ellipse cx="352" cy="600" rx="243" ry="306" fill="url(#scene-glow)"/>
    <ellipse class="scene-edge" cx="352" cy="600" rx="243" ry="306"/>
  </g>

  <text class="brand-name" text-anchor="middle">
    <textPath href="#arc-top" startOffset="50%">DUNMORE VALE</textPath>
  </text>

  <text class="varietal" text-anchor="middle">
    <textPath href="#arc-bottom" startOffset="50%">SAUVIGNON BLANC</textPath>
  </text>

  <text class="region" text-anchor="middle" transform="translate(80 592) rotate(-90)">MARLBOROUGH</text>
  <text class="region" text-anchor="middle" transform="translate(625 592) rotate(90)">NEW ZEALAND</text>
</svg>
</body>
</html>
```